Moravel Aesthetic Doctor

I require an elegant, luxurious looking business card for my aesthetic business. I am a doctor and that will set me aside from competitors. I am planning to provide home and spa based treatments to clients with high expectations. I have attached my logo.

```html
<!DOCTYPE html>
<html lang="en">
<head>
<meta charset="utf-8">
<title>Moravel Aesthetic Doctor – Business Card</title>
<link rel="stylesheet" href="https://fonts.googleapis.com/css2?family=Roboto:ital,wght@0,300;0,400;1,300&display=swap">
<style>
  :root {
    --page-bg: #ece7e1;
    --card-bg: #e4e2df;
    --card-edge: #f4f3f1;
    --ink: #2b2b2b;
    --accent: #3d9ac4;
    --band-start: #2f8fbd;
    --band-end: #4a9ec6;
    --band-text: #c98b84;
    --icon: #4a9ec6;
    --mark-tone: #f3f2f0;
  }
  * { box-sizing: border-box; margin: 0; padding: 0; }
  html, body {
    width: 1200px; height: 1054px; overflow: hidden;
    background: var(--page-bg);
    font-family: "Roboto", Arial, sans-serif;
  }
  .business-card {
    position: absolute; left: 120px; top: 238px;
    width: 960px; height: 578px;
    background: var(--card-bg);
    border: 1px solid var(--card-edge);
    border-radius: 22px;
    overflow: hidden;
    box-shadow: 0 10px 30px rgba(0,0,0,0.08);
  }
  .brand-decoration {
    position: absolute; left: 535px; top: 12px;
    width: 425px; height: 440px;
    background: radial-gradient(ellipse at 60% 45%, rgba(255,255,255,0.55), rgba(255,255,255,0) 70%);
  }
  .doctor-name {
    position: absolute; left: 55px; top: 90px;
    font-size: 37px; font-weight: 300; color: var(--ink);
  }
  .credentials {
    position: absolute; left: 56px; top: 145px;
    font-size: 17px; font-style: italic; font-weight: 300; color: var(--accent);
  }
  .diploma {
    position: absolute; left: 55px; top: 173px;
    font-size: 23px; font-weight: 400; color: var(--accent);
  }
  .contact-list {
    position: absolute; left: 55px; top: 380px;
    list-style: none;
  }
  .contact-item {
    display: flex; align-items: center;
    height: 36px;
    font-size: 23px; font-weight: 400; color: var(--ink);
  }
  .contact-icon { width: 20px; height: 20px; margin-right: 18px; fill: var(--icon); }
  .follow-line {
    position: absolute; left: 55px; top: 486px;
    display: flex; align-items: center;
    font-size: 22px; color: var(--ink);
  }
  .follow-handle { margin-left: 10px; color: var(--ink); }
  .service-band {
    position: absolute; left: 340px; top: 481px;
    width: 620px; height: 51px;
    background: linear-gradient(90deg, var(--band-start), var(--band-end));
    border-radius: 26px 0 0 26px;
    display: flex; align-items: center; justify-content: center;
    font-size: 23px; font-weight: 400; color: var(--band-text);
  }
</style>
</head>
<body>
  <section class="business-card">
    <div class="brand-decoration" role="img" aria-label="Faint brand mark of Moravel Aesthetic Doctor"></div>

    <h1 class="doctor-name">Dr Elena Marsh</h1>
    <p class="credentials">MRCPCH MD</p>
    <p class="diploma">Australasian Diploma of Aesthetic Medicine</p>

    <ul class="contact-list">
      <li class="contact-item">
        <svg class="contact-icon" viewBox="0 0 24 24" aria-hidden="true"><path d="M6.6 10.8a15.1 15.1 0 0 0 6.6 6.6l2.2-2.2a1 1 0 0 1 1-.25 11.4 11.4 0 0 0 3.6.57 1 1 0 0 1 1 1V20a1 1 0 0 1-1 1A17 17 0 0 1 3 4a1 1 0 0 1 1-1h3.5a1 1 0 0 1 1 1c0 1.25.2 2.45.57 3.57a1 1 0 0 1-.25 1z"/></svg>
        0800 555 014
      </li>
      <li class="contact-item">
        <svg class="contact-icon" viewBox="0 0 24 24" aria-hidden="true"><path d="M3 5h18v14H3z M4.5 6.5v.4l7.5 5.6 7.5-5.6v-.4z M4.5 8.8v8.7h15V8.8L12 14.4z" fill-rule="evenodd"/></svg>
        elena@moravel.co.nz
      </li>
      <li class="contact-item">
        <svg class="contact-icon" viewBox="0 0 24 24" aria-hidden="true"><circle cx="12" cy="12" r="9" fill="none" stroke="#4a9ec6" stroke-width="1.6"/><ellipse cx="12" cy="12" rx="4" ry="9" fill="none" stroke="#4a9ec6" stroke-width="1.4"/><path d="M3 12h18M5 7.5h14M5 16.5h14" stroke="#4a9ec6" stroke-width="1.4"/></svg>
        www.moravel.co.nz
      </li>
    </ul>

    <p class="follow-line">Follow us on: <span class="follow-handle">@moravel</span></p>

    <div class="service-band">Home &amp; Spa Based Treatments</div>
  </section>
</body>
</html>
```